Road Construction Company needs business cards

We would like a new business card designed for our business.

We're a road construction company based in Qld, Australia.

Can the business card please have the following information on it.

Name: Warren Halbeck
Position: General Manager
Phone: 0472 915 348
Email: Warren.halbeck@tovrin.com.au
Address: 87 Marrow Ave, Pendlebay, QLD, 4023
Website: www.tovrin.com.au

Visually we'd like the card to be professional and simple.

Attached is our logo.

Our website is www.tovrin.com.au

Target Market(s)

Men aged 25-60

Contact Information for Business Card

As listed in project description

Font styles to use
Serif

Requirements
Must have
• Large logo on back of card

```html
<!DOCTYPE html>
<html lang="en">
<head>
<meta charset="utf-8">
<title>Tovrin Road Construction – Business Card</title>
<link href="https://fonts.googleapis.com/css2?family=Open+Sans:wght@400;600;700;800&display=swap" rel="stylesheet">
<style>
  :root {
    --backdrop: #232323;
    --brand-blue: #1255a5;
    --accent-blue: #3a9ad9;
    --ink: #1a1a1a;
    --paper: #ffffff;
    --shade-dark: #d4d4d6;
    --shade-light: #f6f6f7;
  }
  * { margin: 0; padding: 0; box-sizing: border-box; }
  html, body { width: 1200px; height: 780px; overflow: hidden; }
  body {
    background: var(--backdrop);
    font-family: "Open Sans", Arial, sans-serif;
    position: relative;
  }
  .card {
    position: absolute;
    top: 90px;
    width: 343px;
    height: 600px;
    overflow: hidden;
  }
  .card--back {
    left: 215px;
    background: var(--brand-blue);
  }
  .card--front {
    left: 642px;
    background: var(--paper);
  }

  /* Back */
  .back-wordmark {
    position: absolute;
    left: 50%;
    top: 50%;
    transform: translate(-50%, -50%) rotate(-90deg);
    color: var(--paper);
    font-weight: 800;
    font-size: 96px;
    letter-spacing: 4px;
    white-space: nowrap;
  }

  /* Front */
  .front-wordmark {
    position: absolute;
    top: 58px;
    width: 100%;
    text-align: center;
    color: var(--brand-blue);
    font-weight: 800;
    font-size: 46px;
    letter-spacing: 3px;
  }
  .front-shapes { position: absolute; inset: 0; }
  .contact {
    position: absolute;
    top: 205px;
    width: 100%;
    text-align: center;
  }
  .person-name {
    font-weight: 700;
    font-size: 27px;
    line-height: 1.1;
    text-transform: uppercase;
    color: var(--brand-blue);
  }
  .person-name .surname { color: var(--accent-blue); }
  .person-role {
    font-weight: 600;
    font-size: 14px;
    color: var(--ink);
    margin-top: 2px;
  }
  .contact-icons {
    display: flex;
    justify-content: center;
    gap: 6px;
    margin: 10px 0 6px;
  }
  .contact-icons svg { width: 22px; height: 22px; display: block; }
  .contact-line {
    font-size: 13.5px;
    color: var(--ink);
    line-height: 1.45;
  }
  .address {
    position: absolute;
    bottom: 46px;
    width: 100%;
    text-align: center;
    font-size: 14px;
    line-height: 1.35;
    color: var(--ink);
  }
  .address svg { width: 22px; height: 22px; display: block; margin: 0 auto 8px; }
</style>
</head>
<body>

  <section class="card card--back" aria-label="Card back">
    <div class="back-wordmark">TOVRIN</div>
  </section>

  <section class="card card--front" aria-label="Card front">
    <svg class="front-shapes" viewBox="0 0 343 600" aria-hidden="true">
      <defs>
        <linearGradient id="shade" x1="0" y1="0" x2="0" y2="1">
          <stop offset="0" stop-color="var(--shade-dark)"/>
          <stop offset="1" stop-color="var(--shade-light)"/>
        </linearGradient>
        <filter id="soft-shadow" x="-20%" y="-20%" width="140%" height="140%">
          <feDropShadow dx="0" dy="4" stdDeviation="6" flood-color="#000" flood-opacity="0.22"/>
        </filter>
        <filter id="lift-shadow" x="-20%" y="-20%" width="140%" height="140%">
          <feDropShadow dx="0" dy="-3" stdDeviation="6" flood-color="#000" flood-opacity="0.16"/>
        </filter>
      </defs>
      <rect class="shade-band" x="0" y="300" width="343" height="300" fill="url(#shade)"/>
      <path class="lower-panel" d="M0 600 V520 Q210 480 343 380 V600 Z" fill="var(--paper)" filter="url(#lift-shadow)"/>
      <path class="upper-panel" d="M0 0 H343 V330 Q280 450 0 430 Z" fill="var(--paper)" filter="url(#soft-shadow)"/>
    </svg>

    <div class="front-wordmark">TOVRIN</div>

    <div class="contact">
      <div class="person-name">Warren <span class="surname">Halbeck</span></div>
      <div class="person-role">General Manager</div>
      <div class="contact-icons">
        <svg viewBox="0 0 24 24" aria-label="Phone" role="img">
          <circle cx="12" cy="12" r="12" fill="var(--brand-blue)"/>
          <path d="M8.5 6.5l2 2.2-1.2 1.5c.8 1.7 2 2.9 3.7 3.7l1.5-1.2 2.2 2-1.3 1.8c-4 .2-8-3.8-7.8-7.8z" fill="#fff"/>
        </svg>
        <svg viewBox="0 0 24 24" aria-label="Email" role="img">
          <circle cx="12" cy="12" r="12" fill="var(--brand-blue)"/>
          <rect x="6" y="8" width="12" height="8.5" rx="1" fill="#fff"/>
          <path d="M6.5 8.5l5.5 4.3 5.5-4.3" fill="none" stroke="var(--brand-blue)" stroke-width="1.1"/>
        </svg>
        <svg viewBox="0 0 24 24" aria-label="Website" role="img">
          <circle cx="12" cy="12" r="12" fill="var(--brand-blue)"/>
          <circle cx="12" cy="12" r="6" fill="none" stroke="#fff" stroke-width="1.3"/>
          <ellipse cx="12" cy="12" rx="2.6" ry="6" fill="none" stroke="#fff" stroke-width="1.1"/>
          <path d="M6 12h12" stroke="#fff" stroke-width="1.1"/>
        </svg>
      </div>
      <div class="contact-line">0472 915 348</div>
      <div class="contact-line">www.tovrin.com.au</div>
      <div class="contact-line">Warren.halbeck@tovrin.com.au</div>
    </div>

    <div class="address">
      <svg viewBox="0 0 24 24" aria-label="Location" role="img">
        <circle cx="12" cy="12" r="12" fill="var(--brand-blue)"/>
        <path d="M12 5.5a4 4 0 0 0-4 4c0 3 4 7.5 4 7.5s4-4.5 4-7.5a4 4 0 0 0-4-4z" fill="#fff"/>
        <circle cx="12" cy="9.5" r="1.5" fill="var(--brand-blue)"/>
      </svg>
      87 Marrow Ave,<br>Pendlebay, QLD, 4023
    </div>
  </section>

</body>
</html>
```